Business Card Design

I already have a company logo for my company. I have a logo for the manufacturer we represent. I want a professional business card design.

```html
<!DOCTYPE html>
<html lang="en">
<head>
<meta charset="utf-8">
<title>Beacon Alert Group – Business Card</title>
<link href="https://fonts.googleapis.com/css2?family=Poppins:wght@400;700&display=swap" rel="stylesheet">
<style>
  :root {
    --stage: #b0b0b0;
    --alert-red: #e1061a;
    --caution-gold: #d4a012;
    --ink-black: #000000;
    --paper-white: #ffffff;
  }
  * { margin: 0; padding: 0; box-sizing: border-box; }
  html, body { width: 1093px; height: 1200px; overflow: hidden; }
  body {
    position: relative;
    background: var(--stage);
    font-family: "Poppins", sans-serif;
    color: var(--paper-white);
  }
  .card {
    position: absolute;
    left: 264px;
    width: 580px;
    height: 358px;
    border-radius: 24px;
    overflow: hidden;
  }
  .card-front { top: 226px; background: var(--alert-red); }
  .card-back { top: 621px; background: var(--ink-black); }

  .gold-panel {
    position: absolute;
    top: 0; right: 0;
    width: 160px; height: 100%;
    background: var(--caution-gold);
  }
  .holder-name {
    position: absolute; left: 40px; top: 46px;
    font-weight: 700; font-size: 22px; line-height: 1;
    letter-spacing: 0.2px;
  }
  .holder-title {
    position: absolute; left: 40px; top: 69px;
    font-size: 16.5px; line-height: 1;
  }
  .divider {
    position: absolute; left: 40px;
    width: 67px; height: 1px;
    background: var(--paper-white);
  }
  .divider-top { top: 118px; }
  .divider-bottom { top: 234px; }

  .contact-list {
    position: absolute; left: 40px; top: 144px;
    list-style: none;
    font-size: 17px; line-height: 21px;
  }
  .contact-list li { display: flex; align-items: center; gap: 7px; }
  .contact-list svg { width: 15px; height: 15px; flex: none; }

  .address {
    position: absolute; left: 40px; top: 268px;
    font-size: 17px; line-height: 21px; font-style: normal;
  }

  .front-brand {
    position: absolute; left: 300px; top: 130px;
    width: 250px;
    text-align: center;
    font-weight: 700; font-size: 34px; line-height: 40px;
    color: var(--paper-white);
  }

  .back-brand {
    position: absolute; left: 0; top: 0;
    width: 100%; height: 100%;
    display: flex; align-items: center; justify-content: center; gap: 14px;
    font-weight: 700; font-size: 36px; line-height: 1;
    color: var(--paper-white);
  }
  .brand-mark {
    width: 22px; height: 22px;
    background: var(--alert-red);
  }
</style>
</head>
<body>

  <section class="card card-front" aria-label="Card front">
    <div class="gold-panel"></div>

    <h1 class="holder-name">DANIEL HARPER</h1>
    <p class="holder-title">Managing Director</p>

    <div class="divider divider-top"></div>

    <ul class="contact-list">
      <li>
        <svg viewBox="0 0 24 24" aria-hidden="true"><path fill="#fff" d="M6.6 10.8a15.1 15.1 0 0 0 6.6 6.6l2.2-2.2c.3-.3.7-.4 1-.2 1.1.4 2.3.6 3.6.6.6 0 1 .4 1 1V20c0 .6-.4 1-1 1A17 17 0 0 1 3 4c0-.6.4-1 1-1h3.5c.6 0 1 .4 1 1 0 1.3.2 2.5.6 3.6.1.3 0 .7-.2 1z"/></svg>
        044-555 010 274
      </li>
      <li>
        <svg viewBox="0 0 24 24" aria-hidden="true"><rect x="2" y="5" width="20" height="14" fill="#fff"/><path d="M2 5l10 8 10-8" fill="none" stroke="#e1061a" stroke-width="1.6"/></svg>
        info@beaconalert.com
      </li>
      <li>
        <svg viewBox="0 0 24 24" aria-hidden="true"><g fill="none" stroke="#fff" stroke-width="1.6"><circle cx="12" cy="12" r="10"/><ellipse cx="12" cy="12" rx="4.5" ry="10"/><path d="M2 12h20M4 7h16M4 17h16"/></g></svg>
        www.beaconalert.com
      </li>
    </ul>

    <div class="divider divider-bottom"></div>

    <address class="address">18 Harbour Road, Unit 4<br>40210, Northland</address>

    <div class="front-brand">BEACON<br>ALERT</div>
  </section>

  <section class="card card-back" aria-label="Card back">
    <div class="back-brand">
      <span class="brand-mark"></span>
      <span>BEACON ALERT GROUP</span>
    </div>
  </section>

</body>
</html>
```